Business cards and stationary design

We just completed the design of our new logo and we need to print new business cards and letterhead for our nonprofit. We are looking for a fresh new design that shows off our new logo. On letterhead, we must have a column on the right or left to include our Board of Directors (up to 45 names) (see attachment)

Industry/Entity Type

Non-Profit

Contact Information for Business Card

Standard business card with name, title, Company name, mailing address phone numbers, email address and website. Tagline on back "Bringing the homeless home"

Font styles to use
Sans Serif

Requirements
Must have
• include pertinent information above
• new logo
• fonts compatible with logo
• should use logo colors only
Nice to have
• tag lines

```html
<!DOCTYPE html>
<html lang="en">
<head>
<meta charset="utf-8">
<title>Open Door Housing – Letterhead</title>
<link rel="stylesheet" href="https://fonts.googleapis.com/css2?family=Roboto:wght@400;500;700&family=Didact+Gothic&display=swap">
<style>
  :root {
    --backdrop: #dcdcdc;
    --paper: #f1f1f1;
    --paper-edge: #e4e4e4;
    --ink: #3c3c3c;
    --ink-soft: #555555;
    --rule: #8a8a8a;
    --signature-blue: #c9d8ee;
  }
  * { margin: 0; padding: 0; box-sizing: border-box; }
  html, body {
    width: 1024px; height: 1200px; overflow: hidden;
    background: var(--backdrop);
  }
  .letterhead {
    position: absolute; left: 112px; top: 40px;
    width: 800px; height: 1121px;
    background: linear-gradient(100deg, var(--paper) 0%, var(--paper-edge) 100%);
    box-shadow: 0 2px 10px rgba(0,0,0,0.12);
    font-family: "Roboto", Arial, sans-serif;
    color: var(--ink);
  }
  .brand-name {
    position: absolute; left: 79px; top: 128px;
    font-family: "Roboto", Arial, sans-serif;
    font-weight: 500; font-size: 20px; line-height: 24px;
    color: var(--ink);
  }
  .sender {
    position: absolute; right: 76px; top: 69px;
    text-align: right; font-size: 12px; line-height: 13.8px;
    font-style: normal; color: var(--ink-soft);
  }
  .sender-contact { margin-top: 7px; }
  .board {
    position: absolute; left: 82px; top: 266px; width: 180px;
    font-size: 12px; line-height: 15.8px; color: var(--ink-soft);
  }
  .board-title { font-weight: 500; color: var(--ink); margin-bottom: 15.8px; }
  .board-officers, .board-members { list-style: none; }
  .board-officers strong { font-weight: 500; color: var(--ink); }
  .board-members { margin-top: 15.8px; }
  .column-rule {
    position: absolute; left: 272px; top: 266px;
    width: 1px; height: 683px; background: var(--rule);
  }
  .letter {
    position: absolute; left: 347px; top: 269px; width: 381px;
    font-family: "Didact Gothic", "Century Gothic", sans-serif;
    color: var(--ink-soft);
  }
  .salutation { font-size: 20px; line-height: 24px; color: var(--ink); margin-bottom: 34px; }
  .letter p {
    font-size: 11.6px; line-height: 15.6px; text-align: justify;
    hyphens: auto; margin-bottom: 19px;
  }
  .closing {
    position: absolute; left: 347px; top: 874px;
    font-family: "Didact Gothic", sans-serif; font-size: 11.6px; line-height: 14px;
    color: var(--ink-soft);
  }
  .signature {
    position: absolute; left: 342px; top: 894px;
    width: 120px; height: 58px; border-radius: 6px;
    background: var(--signature-blue);
  }
</style>
</head>
<body>
  <main class="letterhead">
    <header>
      <div class="brand-name">Open Door Housing</div>
      <address class="sender">
        <div>OPEN DOOR HOUSING<br>4120 Birchwood Lane<br>Fairbanks, Alaska 99701</div>
        <div class="sender-contact">555 214 7730<br>mark@opendoorhousing.org<br>www.opendoorhousing.org</div>
      </address>
    </header>

    <aside class="board">
      <div class="board-title">Board of Directors:</div>
      <ul class="board-officers">
        <li><strong>Ralph Denmore</strong>,Chair</li>
        <li><strong>Neil Harmon</strong>,Vice Chair</li>
        <li><strong>Tia Brookner</strong>,Treasurer</li>
        <li><strong>Joy Arden</strong>, Secretary</li>
      </ul>
      <ul class="board-members">
        <li>Glen Abbott</li><li>Paul Beck</li><li>Ray Bloomfield</li><li>Clara Bristow</li>
        <li>Sam Burnett</li><li>Owen Carver</li><li>Margot Chesley</li><li>Dylan Cowell</li>
        <li>Nora Dale</li><li>Evelyn Garrick</li><li>Priya Gulati</li><li>Ivy Grant</li>
        <li>Wade Halloran</li><li>Luke Halloran</li><li>Rachel Hartley</li><li>Troy Hale</li>
        <li>Adam Hollis</li><li>Vera Huxley</li><li>Stacy Hume</li><li>Louisa Jarvis</li>
        <li>Hannah Lowry</li><li>Janet Marlowe</li><li>Frank Northcott</li><li>Peter Pavlik</li>
        <li>Mark Pendleton</li><li>Caroline Shepley</li><li>Grant Sokolov</li><li>Mina Sorensen</li>
        <li>Wendy Stratton</li><li>Gina Moreau</li><li>Monica Thornbury</li><li>Farzana Vellani</li>
        <li>Brenda Walsh</li><li>Derek Wynne</li><li>Ruth Yardley</li><li>Victor Zanetti</li>
      </ul>
    </aside>

    <div class="column-rule"></div>

    <section class="letter">
      <div class="salutation">Dear Mr. Carter,</div>
      <p>Lorem ipsum dolor sit amet, consectetur adipiscing elit. Donec orci purus, luctus vitae dignissim eu, iaculis sed purus. Vivamus faucibus, ipsum nec aliquet viverra, leo mauris condimentum ligula, sit amet sagittis enim ligula quis arcu. Nam egestas tortor id nisi porttitor mattis. In tortor ante, ultricies in suscipit a, tempus non massa. Vivamus et auctor mi. Fusce vel massa nulla. Phasellus nec eros mauris, et scelerisque orci.</p>
      <p>Donec malesuada orci vitae nulla accumsan porta a id massa. Quisque accumsan iaculis magna sit amet fringilla. Maecenas consequat, magna eget tincidunt semper, odio nibh rutrum mi, id feugiat ante nisi eu risus. Vestibulum nunc orci, rhoncus a placerat in, ultricies in mi. Cras mattis varius eros, vel fringilla nisi suscipit eget. Quisque scelerisque sagittis nulla at porttitor.</p>
      <p>Sed id augue vitae urna euismod commodo aliquet a quam. Pellentesque arcu velit, cursus et malesuada ut, consequat et diam. Nullam erat sem, rhoncus id ullamcorper vitae, rhoncus et arcu. In ultricies ultricies nulla, ut rutrum nisi iaculis at. Donec eu magna a metus ornare faucibus. Fusce aliquet faucibus ultricies. Morbi semper, est id tincidunt gravida, sem arcu adipiscing lacus, ac bibendum nulla leo eu purus. Quisque nec diam sed risus consectetur a ccumsan quis quis nibh. Vestibulum id purus lorem.</p>
      <p>It is a long established fact that a reader will be distracted by the readable content of a page when looking at its layout. The point of using Lorem Ipsum is that it has a more-or-less normal distribution of letters, as opposed to using 'Content here, content here', making it look like readable English. Many desktop publishing packages</p>
    </section>

    <div class="closing">Sincerely,</div>
    <div class="signature" role="img" aria-label="Handwritten signature of Mark Ellison"></div>
  </main>
</body>
</html>
```